Sustainably Transforming Education

Company is education services based. early learning through adult and corporate. Focus is national government policy and program design and delivery alongside a research based and academically grounded set of approaches to planning, evaluation, and change management.I am looking for an innovative design position that aligns with the global agendas for innovation, creativity and collaboration at international and national policy levels (berulo is a name that reflects these qualities - colours need to reflect amythyst in some way). I also need a design that translates from a business card as 1 medium of interaction to a template that can work in word/powerpoint etc to support both stationery as well as a digital strategy across multiple channels (fb/twit/etc)There is no slogan/tag line for the company and their is no logo. I was looking to just leverage the name - have currently played around with various fonts (ending up with cuisine - all lowercase).

Industry/Entity Type

Adult

Contact Information for Business Card

name: berulo (all lowercase)Chairman: Andrew CrowMobile: +61 418 902 131Web: www.berulo.comemail: martin.pelly@berulo-example.com

Font styles to use
Script
Other font styles liked:
• cuisine

Colors
e34298
e667a6
33a6d7
aaaaaa

Requirements
Nice to have
• https://files.example-share.net/sh/qx7kw2hd91lzmnp/AAFr3tYbQeLp8VwZnKcDs2Hu?dl=0
• Link to the printwell templates used to begin this process....the one with the lines was about people intersecting (collaborating).....the organic shapes one more of a fluid feel of people coming together - the overall shape being largely spherical could represent a "global" feel.....anyway that is how I was thinking about these

```html
<!DOCTYPE html>
<html lang="en">
<head>
<meta charset="utf-8">
<title>Martin Pelly – Business Card</title>
<link rel="stylesheet" href="https://fonts.googleapis.com/css2?family=Courgette&display=swap">
<style>
  :root {
    --ink-night: #0b0a1c;
    --amethyst-blue: #5a5fc4;
    --amethyst-violet: #7a4fb8;
    --magenta: #e34298;
    --rose: #e667a6;
    --label-bg: #353535;
    --label-text: #ffffff;
  }
  * { margin: 0; padding: 0; box-sizing: border-box; }
  html, body {
    width: 1200px;
    height: 741px;
    overflow: hidden;
    background: var(--ink-night);
  }
  .card {
    position: relative;
    width: 1200px;
    height: 741px;
    overflow: hidden;
    font-family: "Courgette", cursive;
    color: var(--label-text);
  }
  .network-backdrop {
    position: absolute;
    inset: 0;
    background:
      radial-gradient(circle at 50% 40%, rgba(230,103,166,0.55) 0%, transparent 28%),
      radial-gradient(circle at 12% 22%, rgba(90,95,196,0.7) 0%, transparent 30%),
      radial-gradient(circle at 85% 55%, rgba(122,79,184,0.65) 0%, transparent 35%),
      radial-gradient(circle at 20% 80%, rgba(227,66,152,0.5) 0%, transparent 32%),
      radial-gradient(circle at 70% 95%, rgba(90,95,196,0.6) 0%, transparent 30%),
      radial-gradient(circle at 95% 10%, rgba(227,66,152,0.45) 0%, transparent 25%),
      linear-gradient(135deg, #24235e 0%, var(--ink-night) 45%, #2b1d55 100%);
  }
  .identity {
    position: absolute;
    top: 81px;
    right: 76px;
    display: flex;
    flex-direction: column;
    align-items: flex-end;
    gap: 11px;
  }
  .label {
    background: var(--label-bg);
    line-height: 1;
    white-space: nowrap;
  }
  .person-name {
    font-size: 90px;
    padding: 6px 12px 4px 24px;
    height: 108px;
    display: flex;
    align-items: center;
  }
  .person-role {
    font-size: 42px;
    padding: 5px 10px 7px 12px;
  }
  .contact {
    position: absolute;
    top: 495px;
    right: 76px;
    display: flex;
    flex-direction: column;
    align-items: flex-end;
    gap: 4px;
  }
  .contact-line {
    font-size: 25px;
    padding: 7px 10px 8px 10px;
  }
</style>
</head>
<body>
  <main class="card">
    <div class="network-backdrop" role="img" aria-label="Abstract network of intersecting blue, violet and magenta lines representing people collaborating"></div>

    <header class="identity">
      <h1 class="label person-name">Martin Pelly</h1>
      <p class="label person-role">Chairman</p>
    </header>

    <address class="contact">
      <span class="label contact-line">+61 427 315 086</span>
      <span class="label contact-line">martin.pelly@berulo-example.com</span>
      <span class="label contact-line">www.berulo-example.com</span>
    </address>
  </main>
</body>
</html>
```